Honey Company from Florida Needs Sweet and Buzz-worthy Site

Website Requests:
-Deluxe 5-Page Website with SSL-Secure Online Store (Shopify)
-High-end imagery to appeal to a discerning consumer
-Detailed verbiage with strong SEO and easy readability
-Design principles: simple, chic, luxe, earthy
Pages:
1. Home {Local, Raw American Honey from Florida}
2. The Hive
> About Us
>Meet the Beekeepers
3. Buy Honey
> Shopify retail store
4. The Buzz {News, Recipes & More}
> Blog
5. Contact Us {We're Buzzin' to Meet You}
> Store Hours
> Phone Number
> Address
> Quick Contact Form
Attachments: Web design notes, Logo, Color Codes, Inspiration Photos
Target Market(s)
High-end honey consumer in the U.S.
Industry/Entity Type
Upscale honey enthusiasts; direct to consumer sales.
Coding
Coded - Design and coding required
Number of Pages Required
5+ page
Requirements
Must have
- Upscale look and feel, easy usability for quick sales.

```html
<!DOCTYPE html>
<html lang="en">
<head>
<meta charset="utf-8">
<title>Amberfield Honey Co.</title>
<link rel="stylesheet" href="https://fonts.googleapis.com/css2?family=Bitter:wght@400;500;600&family=Lato:wght@400;700&display=swap">
<style>
  :root {
    --hero-bg: #fcf5dc;
    --page-bg: #fbfaf3;
    --ink: #1c1a16;
    --body-ink: #2f2c26;
    --gold: #f0c84a;
    --gold-line: #f1dba6;
    --logo-ring: #26231d;
  }
  * { box-sizing: border-box; margin: 0; padding: 0; }
  html, body { width: 1200px; height: 2892px; overflow: hidden; }
  body {
    position: relative;
    background: var(--page-bg);
    color: var(--body-ink);
    font-family: "Lato", Arial, sans-serif;
    font-size: 15px;
    line-height: 21.8px;
  }
  .abs { position: absolute; }
  h1, h2, h3 { font-family: "Bitter", Georgia, serif; color: var(--ink); font-weight: 500; }

  .hero { left: 0; top: 0; width: 1200px; height: 662px; background: var(--hero-bg); }
  .brand { left: 131px; top: 35px; width: 156px; height: 156px; border-radius: 50%;
    border: 2px solid var(--logo-ring); display: flex; align-items: center; justify-content: center; text-align: center; }
  .brand-name { font-family: "Bitter", Georgia, serif; font-weight: 600; font-size: 19px; line-height: 22px; color: var(--ink); }
  .nav { top: 33px; left: 566px; display: flex; gap: 0; font-family: "Bitter", Georgia, serif; font-size: 18px; color: var(--ink); }
  .nav a { color: inherit; text-decoration: none; position: absolute; white-space: nowrap; }
  .hero-title { left: 131px; top: 326px; font-size: 50px; line-height: 71px; font-weight: 500; }
  .hero-photo { left: 578px; top: 146px; width: 600px; height: 471px;
    background: radial-gradient(ellipse at 55% 55%, #b5651d 0%, #d49a52 35%, #e9cfa0 62%, rgba(252,245,220,0) 80%); }

  .section-title { font-size: 27px; line-height: 34px; }
  .section-sub { font-family: "Bitter", Georgia, serif; font-size: 15px; color: var(--ink); }
  .fact { width: 427px; }
  .fact-right { width: 400px; }
  .rule { height: 1px; background: var(--gold-line); width: 427px; }

  .photo { display: block; }
  .photo-beekeepers { left: 131px; top: 1413px; width: 453px; height: 402px;
    background: linear-gradient(180deg, #6f9fd8 0%, #a9c7ea 38%, #7f9a52 62%, #5d7134 100%); }
  .photo-frames { left: 614px; top: 1897px; width: 452px; height: 401px;
    background: linear-gradient(160deg, #5c7a34 0%, #8b5a2b 30%, #c7762e 55%, #5a4632 85%, #3f3a33 100%); }
  .about-copy p, .health-copy p { margin-bottom: 21.8px; }

  .feed-title { left: 0; width: 1200px; top: 2360px; text-align: center; font-size: 27px; }
  .feed-tile { top: 2436px; width: 225px; height: 210px; }
  .tile-1 { left: 12px; background: linear-gradient(180deg, #3b5a7a 0%, #e7b92a 70%, #1f2b3a 100%); }
  .tile-2 { left: 249px; background: linear-gradient(150deg, #3d4a22 0%, #6b4a30 50%, #2b2b26 100%); }
  .tile-3 { left: 489px; background: linear-gradient(180deg, #efe7d8 0%, #c7731b 55%, #e3a43b 100%); }
  .tile-4 { left: 726px; background: linear-gradient(180deg, #c9d3db 0%, #6a7d4e 45%, #e8e8e4 70%, #55524a 100%); }
  .tile-5 { left: 963px; background: linear-gradient(180deg, #5a2c10 0%, #a8561a 50%, #d9c88a 100%); }

  .footer-title { font-size: 27px; }
  .email-field { left: 589px; top: 2758px; width: 326px; height: 32px; border-bottom: 1.5px solid var(--gold);
    font-size: 14px; color: var(--ink); }
  .subscribe { left: 929px; top: 2750px; width: 137px; height: 42px; border: 2px solid var(--gold-line);
    color: var(--gold); font-family: "Bitter", Georgia, serif; font-weight: 600; font-size: 17px;
    display: flex; align-items: center; justify-content: center; background: transparent; }
  .copyright { left: 131px; top: 2828px; font-size: 14px; color: var(--ink); }
</style>
</head>
<body>

<header class="abs hero">
  <div class="abs brand"><span class="brand-name">Amberfield<br>Honey Co.</span></div>
  <nav class="abs nav" style="left:0;top:33px;width:1200px;">
    <a href="#" style="left:566px">Home</a>
    <a href="#" style="left:654px">The Hive</a>
    <a href="#" style="left:767px">Buy Honey</a>
    <a href="#" style="left:897px">The Buzz</a>
    <a href="#" style="left:1004px">Contact</a>
  </nav>
  <h1 class="abs hero-title">Straight from our<br>beloved hives to<br>your lovely home</h1>
  <div class="abs hero-photo" role="img" aria-label="Stacked hexagonal jars of raw honey in kraft paper sleeves"></div>
</header>

<section>
  <h2 class="abs section-title" style="left:130px;top:720px;">Don’t Judge a Bee by Its Stinger</h2>
  <p class="abs section-sub" style="left:130px;top:765px;">If the bee disappeared off the face of the Earth, man would have only four years left to live</p>

  <p class="abs fact" style="left:130px;top:843px;width:360px;">Hyper-efficient insects do play a vital role in agriculture. Almonds, for example, are almost entirely dependent on honeybee pollination</p>
  <p class="abs fact-right" style="left:659px;top:843px;">Over one-third of our entire diet is dependent on pollination from the honeybee. So, for every three bites of food you eat, you can thank the honeybee for one of those three bites,” Warren says.</p>
  <div class="abs rule" style="left:130px;top:955px;"></div>
  <div class="abs rule" style="left:643px;top:955px;"></div>

  <p class="abs fact" style="left:130px;top:986px;width:430px;">They are very misunderstood among the public. We have lost a great amount of our natural forage land due to urbanization and suburban sprawl, and when people and honeybees mix, it’s going to have less than desirable results. I receive complaints about my bees going to neighbors’ swimming pools to gather fresh water to swarms of bees moving into people’s property. You name it, I’ve dealt with it. But it takes patience and mutual understanding on both sides to overcome the obstacles</p>
  <p class="abs fact-right" style="left:659px;top:986px;width:390px;">Without beekeepers and the pollination services their hives provide to growers in the U.S., we would lose a significant yield from many crops, including blueberries, watermelons, zucchinis, and almonds, to name a few, which would cause food prices to rise as the supply<br>would diminish,</p>
  <div class="abs rule" style="left:131px;top:1224px;"></div>
  <div class="abs rule" style="left:645px;top:1224px;"></div>

  <p class="abs fact" style="left:132px;top:1264px;width:380px;">The state’s bees pollinate a variety of crops, from Florida blueberries to California almonds.</p>
  <p class="abs fact-right" style="left:661px;top:1264px;">Play a key role in pollinating crops across the country. For instance, more than 250,000 colonies are shipped each year from Florida to almond growers in California, Mercer said.</p>
</section>

<section>
  <div class="abs photo photo-beekeepers" role="img" aria-label="Two beekeepers in veils holding hive frames in a field of hives"></div>
  <h2 class="abs section-title" style="left:629px;top:1405px;font-size:28px;">About us</h2>
  <div class="abs about-copy" style="left:629px;top:1453px;width:450px;">
    <p>100% raw, unfiltered Florida honey straight from he beehives on his six-acre property, Amberfield Honey Farm, 18420 Orchard Lane<br>in Lake Haven.</p>
    <p>Agricultural Company specializing in the Production of 100% Raw American Honey, and the Pollination of America’s food crops.</p>
    <p>Our Honey comes straight from our beehives to your table. No filtering, heating, or any funny stuff. Just All Natural, 100%<br>Pure Florida Honey</p>
    <p>Natural Wild Honey- flavors include Orange Blossom, Gallberry, Summer Wildflower, Winter Wildflower, and many more.<br>Bee Pollen, Royal Jelly, and Bee venom. Bee removals are done by Warren.</p>
    <p>Halvorsen, owner of Amberfield Honey Farm, has about 1,200 beehives that he moves around to pollinate different plants.</p>
  </div>
</section>

<section>
  <h2 class="abs section-title" style="left:131px;top:1945px;">The health benefits of honey</h2>
  <p class="abs section-sub" style="left:131px;top:1989px;">Real Local Honey, Really Good for You</p>
  <div class="abs health-copy" style="left:132px;top:2040px;width:360px;">
    <p>aw honey is loaded with antioxidants to protect your body from cell damage due to free radicals. Honey has been long known as a folk remedy to help heal burns and wounds due to its antibacterial and antifungal properties. Honey is also very well known to soothe a sore throat. Try taking a spoonful of honey and add it to hot tea if you feel like you have a cold. Honey can also help as a cough suppressant.</p>
  </div>
  <div class="abs photo photo-frames" role="img" aria-label="Open hive boxes showing wax-covered frames with bees"></div>
</section>

<section>
  <h2 class="abs feed-title">Hive Feed</h2>
  <div class="abs feed-tile tile-1" role="img" aria-label="Beeswax candles shaped like owls and hives"></div>
  <div class="abs feed-tile tile-2" role="img" aria-label="Hands lighting a bee smoker"></div>
  <div class="abs feed-tile tile-3" role="img" aria-label="Bottles of raw honey on a counter"></div>
  <div class="abs feed-tile tile-4" role="img" aria-label="Company pickup truck parked among pine trees"></div>
  <div class="abs feed-tile tile-5" role="img" aria-label="Jars of tupelo honey with green labels"></div>
</section>

<footer>
  <h2 class="abs footer-title" style="left:130px;top:2698px;">Contact</h2>
  <p class="abs" style="left:132px;top:2739px;color:var(--ink);font-size:14px;">272 Linden Ave,<br>Cedar Bay, FL 32001<br>555.014.2290</p>
  <h2 class="abs footer-title" style="left:586px;top:2698px;">Newsletter</h2>
  <div class="abs email-field">Email address</div>
  <div class="abs subscribe">Subscribe</div>
  <p class="abs copyright">Copyright © 2021 All Rights Reserved</p>
</footer>

</body>
</html>
```